Crestline Staffing PEO - Web Build for Professional Employment Organization

We need a website built for our new PEO (professional employment organization). This company will offer third party Human Resource services to companies who are looking to outsource:<br/>Recruiting<br/>Administrative Onboarding<br/>New hire training, ongoing training and development<br/>Payroll/compensation processing/services<br/>Employee Relations<br/>Unemployment Claim Facilitation<br/>Benefits Plans and Administration<br/><br/>I have attached the logo below. Please use that as a reference and color match as best as possible. <br/><br/>Here are some of the competitor's websites:<br/>https://www.velmorahr.com/ <br/>https://www.trundelpay.com/<br/>https://www.trundelpay.com/<br/>https://www.qzn.com/<br/>https://www.bremwickhr.com/<br/>https://orvalepeo.com/contact-orvale/<br/><br/>

Target Market(s)

Startups and mid-sized businesses

Number of Pages Required

5+ page

Font styles to use
Sans Serif

Colors
0592cd

Requirements
Must have
• Features Pages
• SEO driven keyword rich content
• Strong focus on our ability to provide unemployment claim facilitation services as well as mandatory training/certification fulfillment
Nice to have
• I'd like to see one mockup with a Live Chat version if possible. In theory, the Live Chat messages would go directly to our front desk person.

```html
<!DOCTYPE html>
<html lang="en">
<head>
<meta charset="utf-8">
<title>Crestline Staffing PEO</title>
<link href="https://fonts.googleapis.com/css2?family=Montserrat:wght@400;500;600&family=Roboto:wght@400&display=swap" rel="stylesheet">
<style>
:root{
  --brand:#0592cd;
  --brand-deep:#1a7fd4;
  --brand-light:#1fb6e8;
  --navy:#0d4a8a;
  --ink:#222;
  --muted:#444;
  --line:#dcdcdc;
  --tile:#f3f3f3;
  --panel:#f3eff0;
  --gold:#f2a516;
  --white:#fff;
}
*{box-sizing:border-box;margin:0;padding:0}
html,body{width:1200px;height:3808px;overflow:hidden}
body{font-family:"Montserrat",sans-serif;color:var(--ink);background:var(--white);position:relative}
.abs{position:absolute}

/* header / hero */
.hero-panel{left:0;top:0;width:680px;height:576px;background:linear-gradient(135deg,var(--brand-deep),var(--brand-light))}
.logo{color:var(--white);font-weight:600;font-size:20px;letter-spacing:1px;line-height:1.1;text-align:center}
.logo small{display:block;font-size:12px;letter-spacing:8px;font-weight:600}
.site-logo{left:93px;top:44px}
.nav{top:50px;left:408px;display:flex;gap:28px;font-size:15px}
.nav a{text-decoration:none;color:var(--white)}
.nav a.dark{color:var(--brand)}
.nav .gap{width:2px}
.socials-top{left:900px;top:51px;display:flex;gap:14px}
.socials-top span{width:10px;height:10px;border-radius:50%;background:var(--brand)}
.login{left:1006px;top:42px;width:103px;height:36px;background:var(--navy);color:var(--white);border-radius:3px;font-size:15px;display:flex;align-items:center;justify-content:center;gap:7px}
.login i{width:13px;height:13px;border:2px solid var(--white);border-radius:50%}
.hero-photo{left:90px;top:111px;width:845px;height:378px;background:linear-gradient(120deg,#2c5b78 0%,#1f4e6a 45%,#3e7080 100%)}
.hero-title{left:119px;top:246px;color:var(--white);font-size:33px;font-weight:500;line-height:44px}
.hero-arrows{left:94px;top:520px;display:flex;gap:18px}

/* section titles */
.section-title{width:1200px;text-align:center;font-size:40px;font-weight:500}
.lead{width:1200px;text-align:center;font-size:16px;color:var(--muted);line-height:34px}

/* services grid */
.services{left:89px;top:878px;width:1024px;display:grid;grid-template-columns:repeat(3,1fr);gap:2px;background:var(--line);border:2px solid var(--line)}
.service{height:222px;background:var(--tile);display:flex;flex-direction:column;align-items:center;padding-top:18px;text-align:center;font-size:18px;font-weight:500;line-height:33px;color:var(--ink)}
.service.active{background:#f8f8fb;color:var(--brand)}
.service .ico{width:70px;height:70px;border-radius:50%;background:linear-gradient(135deg,var(--brand-light),var(--brand-deep));margin-bottom:34px;display:flex;align-items:center;justify-content:center}

/* banner */
.banner{left:0;top:1411px;width:1200px;height:357px;background:linear-gradient(90deg,#2c4a5a 0%,#2f6b78 50%,#5a8a96 100%)}
.banner-text{left:0;top:1525px;width:1200px;text-align:center;color:var(--white);font-size:25px;font-weight:500;line-height:50px}

/* steps */
.step{width:200px;text-align:center;font-size:22px}
.step .disc{width:116px;height:116px;margin:0 auto 28px;border-radius:50%;background:#f2f2f2;border:2px solid #ddd;display:flex;align-items:center;justify-content:center}

/* how we are */
.how-photo{left:0;top:2350px;width:503px;height:500px;background:linear-gradient(135deg,#8fa6a4,#4a6f86 55%,#b8a48a)}
.how-panel{left:503px;top:2375px;width:697px;height:475px;background:var(--panel)}
.how-title{left:544px;top:2440px;font-size:40px;font-weight:500}
.how-lead{left:546px;top:2508px;font-size:16px;color:var(--muted);line-height:36px}
.feature{display:flex;align-items:center;gap:12px;font-size:16px;color:var(--muted)}
.feature .disc{width:64px;height:64px;border-radius:50%;background:var(--white);border:2px solid #e4e4e4;display:flex;align-items:center;justify-content:center}

/* testimonials */
.card{top:3093px;width:330px;height:178px;border:2px solid var(--line);background:var(--white);box-shadow:0 2px 6px rgba(0,0,0,.08)}
.card p{position:absolute;left:56px;top:40px;width:260px;font-size:15px;line-height:25px;color:var(--muted)}
.card .stars{position:absolute;left:56px;top:128px;display:flex;gap:2px}
.card .q{position:absolute;font-family:Georgia,serif;font-size:70px;color:#c4d8ee;line-height:1}
.card .q.open{left:12px;top:4px}
.card .q.close{right:16px;top:118px}
.card .tail{position:absolute;left:66px;bottom:-20px;width:34px;height:34px;background:var(--white);border-right:2px solid var(--line);border-bottom:2px solid var(--line);transform:rotate(45deg) skew(8deg,8deg)}
.client{top:3303px;display:flex;align-items:center;gap:26px}
.client .avatar{width:62px;height:62px;border-radius:50%;background:linear-gradient(135deg,#d9b49a,#7a5a48)}
.client .name{font-size:19px;font-style:italic;color:#888;letter-spacing:.5px}
.client .date{font-size:16px;color:#777;letter-spacing:.5px}

.live-chat{left:1086px;top:3398px;width:114px;height:46px;background:var(--brand-light);color:var(--white);font-size:14px;display:flex;align-items:center;justify-content:center;gap:7px}
.live-chat:after{content:"";position:absolute;left:12px;bottom:-10px;border-left:10px solid var(--brand-light);border-bottom:10px solid transparent}

/* footer */
.footer{left:0;top:3475px;width:1200px;height:333px;background:linear-gradient(100deg,#2a6fd9 0%,#2a9be6 50%,#3ad8ef 100%)}
.footer .logo{position:absolute;left:0;width:1200px;top:90px}
.footer-nav{position:absolute;top:160px;left:0;width:1200px;display:flex;justify-content:center;gap:28px;font-size:15px;color:var(--white)}
.footer-social{position:absolute;top:212px;left:0;width:1200px;display:flex;justify-content:center;gap:22px}
.footer-social span{width:22px;height:22px;border-radius:50%;background:var(--white)}
.copyright{position:absolute;top:280px;left:0;width:1200px;text-align:center;font-family:"Roboto",sans-serif;font-size:14px;color:var(--white)}
</style>
</head>
<body>

<header>
  <div class="abs hero-panel"></div>
  <div class="abs logo site-logo">CRESTLINE STAFFING<small>PEO</small></div>
  <nav class="abs nav">
    <a href="#">HOME</a><a href="#">ABOUT US</a><a href="#">SERVICES</a><span class="gap"></span>
    <a class="dark" href="#">BLOG</a><a class="dark" href="#">CONTACTS</a>
  </nav>
  <div class="abs socials-top" aria-label="social links"><span></span><span></span><span></span></div>
  <div class="abs login"><i></i>LogIn</div>
  <div class="abs hero-photo" role="img" aria-label="HR consultant smiling while interviewing a candidate at a desk"></div>
  <h1 class="abs hero-title">Professional<br>Employment Organization</h1>
  <div class="abs hero-arrows">
    <svg width="20" height="12" viewBox="0 0 20 12"><path d="M19 6H2M6 1L1 6l5 5" stroke="#fff" fill="none" stroke-width="1.2"/></svg>
    <svg width="20" height="12" viewBox="0 0 20 12"><path d="M1 6h17M14 1l5 5-5 5" stroke="#fff" fill="none" stroke-width="1.2"/></svg>
  </div>
</header>

<section>
  <h2 class="abs section-title" style="top:668px">Our Services</h2>
  <p class="abs lead" style="top:740px">Lorem ipsum dolor sit amet, consectetur adipiscing elit, sed do eiusmod tempor incididunt ut<br>labore et dolore magna aliqua. Quis ipsum suspendisse ultrices gravida.</p>
  <div class="abs services">
    <div class="service"><span class="ico"><svg width="36" height="36" viewBox="0 0 36 36"><circle cx="18" cy="16" r="11" fill="none" stroke="#123" stroke-width="2"/><path d="M18 10l2 4 4 .5-3 3 .8 4-3.8-2-3.8 2 .8-4-3-3 4-.5z" fill="none" stroke="#123" stroke-width="1.6"/></svg></span>Recruiting</div>
    <div class="service active"><span class="ico"><svg width="36" height="36" viewBox="0 0 36 36"><circle cx="18" cy="18" r="12" fill="none" stroke="#123" stroke-width="2" stroke-dasharray="4 2"/><path d="M12 18l4 4 8-8" fill="none" stroke="#123" stroke-width="2"/></svg></span>Administrative Onboarding</div>
    <div class="service"><span class="ico"><svg width="36" height="36" viewBox="0 0 36 36"><rect x="9" y="6" width="18" height="24" fill="none" stroke="#123" stroke-width="2"/><circle cx="18" cy="15" r="3.5" fill="none" stroke="#123" stroke-width="1.6"/><path d="M13 24h10" stroke="#123" stroke-width="1.6"/></svg></span>New hire training, ongoing<br>training and development</div>
    <div class="service"><span class="ico"><svg width="36" height="36" viewBox="0 0 36 36"><circle cx="18" cy="15" r="10" fill="none" stroke="#123" stroke-width="2"/><path d="M14 27h8M15 31h6M18 9v12" stroke="#123" stroke-width="1.6"/></svg></span>Payroll/compensation<br>processing/services</div>
    <div class="service"><span class="ico"><svg width="36" height="36" viewBox="0 0 36 36"><circle cx="12" cy="11" r="3" fill="none" stroke="#123" stroke-width="1.6"/><circle cx="18" cy="11" r="3" fill="none" stroke="#123" stroke-width="1.6"/><circle cx="24" cy="11" r="3" fill="none" stroke="#123" stroke-width="1.6"/><path d="M6 24l6-4h10l6 4-8 6H12z" fill="none" stroke="#123" stroke-width="1.8"/></svg></span>Employee Relations</div>
    <div class="service"><span class="ico"><svg width="36" height="36" viewBox="0 0 36 36"><circle cx="12" cy="11" r="3" fill="none" stroke="#123" stroke-width="1.6"/><circle cx="18" cy="11" r="3" fill="none" stroke="#123" stroke-width="1.6"/><circle cx="24" cy="11" r="3" fill="none" stroke="#123" stroke-width="1.6"/><path d="M6 24l6-4h10l6 4-8 6H12z" fill="none" stroke="#123" stroke-width="1.8"/></svg></span>Unemployment Claim<br>Facilitation</div>
  </div>
</section>

<section>
  <div class="abs banner" role="img" aria-label="Hands signing a document with a pen"></div>
  <p class="abs banner-text">With our specialists, and experts at your disposal, you will<br>face complex HR issues with confidence</p>
</section>

<section>
  <h2 class="abs section-title" style="top:1834px">Get Started Today</h2>
  <p class="abs lead" style="top:1904px">Lorem ipsum dolor sit amet, consectetur adipiscing elit, sed do eiusmod tempor incididunt ut labore et<br>dolore magna aliqua. Quis ipsum suspendisse ultrices gravida. Risus commodo viverra maecenas<br>accumsan lacus vel facilisis.</p>
  <div class="abs step" style="left:172px;top:2060px"><div class="disc"><svg width="64" height="64" viewBox="0 0 64 64" fill="none" stroke="#2a7fd8" stroke-width="2"><circle cx="20" cy="42" r="9"/><circle cx="44" cy="42" r="9"/><circle cx="32" cy="20" r="9"/><path d="M12 12h8M44 12h8M26 27l-3 6M38 27l3 6"/></svg></div>CONNECT</div>
  <div class="abs step" style="left:499px;top:2060px"><div class="disc"><svg width="64" height="64" viewBox="0 0 64 64" fill="none" stroke="#2a7fd8" stroke-width="2"><rect x="10" y="10" width="18" height="12" rx="2"/><rect x="36" y="8" width="18" height="12" rx="2"/><path d="M8 44h48M14 44v10M50 44v10"/><circle cx="20" cy="34" r="4"/><circle cx="32" cy="34" r="4"/><circle cx="44" cy="34" r="4"/></svg></div>MEET</div>
  <div class="abs step" style="left:828px;top:2060px"><div class="disc"><svg width="64" height="64" viewBox="0 0 64 64" fill="none" stroke="#2a7fd8" stroke-width="2"><rect x="10" y="8" width="44" height="48"/><rect x="18" y="18" width="12" height="38"/><rect x="34" y="18" width="12" height="38"/><path d="M26 12h12M50 30v6"/></svg></div>ELEVATE</div>
</section>

<section>
  <div class="abs how-photo" role="img" aria-label="Two professionals shaking hands across an office desk"></div>
  <div class="abs how-panel"></div>
  <h2 class="abs how-title">How We Are</h2>
  <p class="abs how-lead">Lorem ipsum dolor sit amet, consectetur adipiscing elit, sed do<br>eiusmod tempor &nbsp;adipiscing elit incididunt ut labore .</p>
  <div class="abs feature" style="left:549px;top:2627px"><span class="disc"><svg width="34" height="34" viewBox="0 0 34 34" fill="none" stroke="#333" stroke-width="1.6"><circle cx="11" cy="10" r="4"/><circle cx="23" cy="10" r="4"/><path d="M5 30V20h24v10M10 20v10M24 20v10"/></svg></span>Lorem ipsum dolor sit</div>
  <div class="abs feature" style="left:853px;top:2627px"><span class="disc"><svg width="34" height="34" viewBox="0 0 34 34" fill="none" stroke="#333" stroke-width="1.6"><rect x="6" y="6" width="22" height="22"/><circle cx="17" cy="17" r="6"/><path d="M6 12h22"/></svg></span>Lorem ipsum dolor sit</div>
  <div class="abs feature" style="left:549px;top:2727px"><span class="disc"><svg width="34" height="34" viewBox="0 0 34 34" fill="none" stroke="#333" stroke-width="1.6"><circle cx="17" cy="17" r="5"/><circle cx="8" cy="8" r="3"/><circle cx="26" cy="8" r="3"/><circle cx="8" cy="26" r="3"/><circle cx="26" cy="26" r="3"/><path d="M10 10l3 3M24 10l-3 3M10 24l3-3M24 24l-3-3"/></svg></span>Lorem ipsum dolor sit</div>
  <div class="abs feature" style="left:853px;top:2727px"><span class="disc"><svg width="34" height="34" viewBox="0 0 34 34" fill="none" stroke="#333" stroke-width="1.6"><path d="M6 30h22M8 30V22h6v-6h6v-6h6v20"/><path d="M22 4v6h5"/></svg></span>Lorem ipsum dolor sit</div>
</section>

<section>
  <h2 class="abs section-title" style="top:2958px;font-size:32px">What Are Our Clients Saying?</h2>

  <div class="abs card" style="left:81px"><span class="q open">&#8220;</span><p>Lorem ipsum dolor sit amet, consectetur adipiscing elit, sed do eiusmod tempor</p><div class="stars"><svg width="90" height="15" viewBox="0 0 90 15"><g fill="#f2a516"><path id="st" d="M7.5 0l2.2 4.8 5.3.6-3.9 3.6 1 5.2-4.6-2.6-4.6 2.6 1-5.2L0 5.4l5.3-.6z"/><use href="#st" x="18"/><use href="#st" x="36"/><use href="#st" x="54"/><use href="#st" x="72"/></g></svg></div><span class="q close">&#8221;</span><span class="tail"></span></div>
  <div class="abs card" style="left:440px"><span class="q open">&#8220;</span><p style="top:48px">Lorem ipsum dolor sit amet, consectetur adipiscing elit, sed do eiusmod tempor</p><div class="stars" style="top:136px"><svg width="90" height="15" viewBox="0 0 90 15"><g fill="#f2a516"><use href="#st"/><use href="#st" x="18"/><use href="#st" x="36"/><use href="#st" x="54"/><use href="#st" x="72"/></g></svg></div><span class="q close">&#8221;</span><span class="tail"></span></div>
  <div class="abs card" style="left:789px"><span class="q open">&#8220;</span><p style="top:48px;left:26px">Lorem ipsum dolor sit amet, consectetur adipiscing elit, sed do eiusmod tempor</p><div class="stars" style="top:136px;left:26px"><svg width="90" height="15" viewBox="0 0 90 15"><g fill="#f2a516"><use href="#st"/><use href="#st" x="18"/><use href="#st" x="36"/><use href="#st" x="54"/><use href="#st" x="72"/></g></svg></div><span class="q close">&#8221;</span><span class="tail"></span></div>

  <div class="abs client" style="left:94px"><span class="avatar" role="img" aria-label="Client portrait"></span><div><div class="name">Lorem ipsum</div><div class="date">20/01/2020</div></div></div>
  <div class="abs client" style="left:452px"><span class="avatar" role="img" aria-label="Client portrait"></span><div><div class="name">Lorem ipsum</div><div class="date">17/01/2020</div></div></div>
  <div class="abs client" style="left:801px"><span class="avatar" role="img" aria-label="Client portrait"></span><div><div class="name">Lorem ipsum</div><div class="date">25/01/2020</div></div></div>

  <div class="abs live-chat"><svg width="20" height="16" viewBox="0 0 20 16" fill="none" stroke="#fff" stroke-width="1.4"><rect x="1" y="1" width="18" height="11" rx="1"/><path d="M5 5h10M5 8h7M5 12v3l3-3"/></svg>Live Chat</div>
</section>

<footer class="abs footer">
  <div class="logo">CRESTLINE STAFFING<small>PEO</small></div>
  <nav class="footer-nav"><span>HOME</span><span>ABOUT US</span><span>SERVICES</span><span>BLOG</span><span>CONTACTS</span></nav>
  <div class="footer-social" aria-label="social links"><span></span><span></span><span></span><span></span></div>
  <p class="copyright">&copy; 2020 All Rights Reserved | Privacy Policy | Terms and Conditions</p>
</footer>

</body>
</html>
```